We’re a real estate firm that has landed a big builder in a neighboring state. Our branding needs...

We are a real estate firm who represents various builders along with doing resale here in Oregon. Our firm is growing to represent a big builder in Washington State and we’ll have another 40 brokers on our team. We need rebranding. As in, a new logo ( the house logo we have now looks cartoonish, hate it). We need new cards, something to really stand out. I’ve been thinking of using those NFC cards from ZEP or the ones with the seam color. I likely want two or three designs, a darker (as in a background color of black or grey) , a light one ( again I mean background color) and a credit card style (either plastic w an embossed name/number on front, or metal ). I’m thinking dark background for cc, or silver if it’s metal. That’s my thoughts, but you are the artists, so maybe you have an idea I haven’t considered. Our colors were black and red, but we don’t have to stick to that. Just nothing too busy. Oh, and we are typically representing the local, higher quality builders in our area (just below custom), but not national. Subdivisions are near the Kell Varney, Brisco, and Thornfield Crest sites. We are super excited, but without a lot of time to change the “look” of our brokerage. So I’ll be deciding and moving forward within 24 hours tops. Our name is Real Estate Summit Alliance ( we cant change the name because of timeline and business license) Thank you!

Industry/Entity Type

Real Estate

Contact Information for Business Card

The usual. Name of firm. Name of cardholder. Contact info.

Font styles to use
Serif
Sans Serif

Colors

Designer to choose colors to be used in the design.

Requirements
Must have
• A sleek or simple look. I included photos of cards with stylistic attributes we like. Thank you
Nice to have
• We really like the black backgrounds. With foil or embossed detail. We also like the black on black. Matte black card with raised shiny black detail. But still eye catching.
Should not have
• No ornate or busy looking style. We don’t want anything cluttered.

```html
<!DOCTYPE html>
<html lang="en">
<head>
<meta charset="utf-8">
<title>Real Estate Summit Alliance – Business Card</title>
<link href="https://fonts.googleapis.com/css2?family=Montserrat:wght@400;500;600;700&display=swap" rel="stylesheet">
<style>
  :root{
    --backdrop:#1b1b1c;
    --card-front:#2b2b2c;
    --card-back:#232324;
    --white:#f4f4f4;
    --red:#e5262b;
    --grey:#8e8e8e;
    --gloss:#4c4c4e;
  }
  *{margin:0;padding:0;box-sizing:border-box}
  html,body{width:1200px;height:865px;overflow:hidden;background:var(--backdrop)}
  body{position:relative;font-family:"Montserrat",Arial,sans-serif;color:var(--white)}
  .card{position:absolute;width:560px;height:320px;border-radius:3px;box-shadow:0 18px 40px rgba(0,0,0,.55)}
  .card-front{left:110px;top:70px;background:var(--card-front)}
  .card-back{left:530px;top:470px;background:var(--card-back)}

  .holder{position:absolute;left:36px;top:42px}
  .holder-name{font-size:19px;font-weight:700;letter-spacing:1px;text-transform:uppercase}
  .holder-name .surname{color:var(--red)}
  .holder-title{font-size:12px;font-weight:500;color:var(--grey);letter-spacing:1.2px;text-transform:uppercase;margin-top:3px}

  .firm{position:absolute;right:36px;top:36px;text-align:right;display:flex;align-items:center;gap:10px}
  .firm-mark{width:14px;height:14px;background:var(--red)}
  .firm-name{font-size:17px;font-weight:600;line-height:1.2;text-transform:uppercase;letter-spacing:1px;color:var(--white)}

  .address{position:absolute;right:36px;top:150px;text-align:right;font-size:12px;line-height:1.45;display:flex;gap:8px;align-items:flex-start}
  .address svg{margin-top:2px}

  .contacts{position:absolute;left:36px;bottom:34px;list-style:none;font-size:12.5px;line-height:1.6}
  .contacts li{display:flex;align-items:center;gap:10px}
  .icon{width:12px;height:12px;fill:var(--red);flex:none}

  .back-firm{position:absolute;left:0;right:0;top:108px;text-align:center;font-size:30px;font-weight:700;line-height:1.15;text-transform:uppercase;letter-spacing:2px;color:var(--gloss)}
  .back-web{position:absolute;left:0;right:0;bottom:34px;text-align:center;font-size:12px;font-weight:600;letter-spacing:2px;text-transform:uppercase;color:var(--gloss)}
</style>
</head>
<body>

<section class="card card-front" aria-label="Business card front">
  <div class="holder">
    <p class="holder-name">Dana <span class="surname">Whitlow</span></p>
    <p class="holder-title">Real Estate Broker</p>
  </div>

  <div class="firm">
    <span class="firm-mark"></span>
    <p class="firm-name">Real Estate<br>Summit Alliance</p>
  </div>

  <div class="address">
    <p>2180 Alder Crest Road, Suite 310<br>Portland, OR 97205</p>
    <svg class="icon" viewBox="0 0 12 12"><path d="M6 0a4 4 0 0 0-4 4c0 3 4 8 4 8s4-5 4-8a4 4 0 0 0-4-4zm0 5.5A1.5 1.5 0 1 1 6 2.5a1.5 1.5 0 0 1 0 3z"/></svg>
  </div>

  <ul class="contacts">
    <li><svg class="icon" viewBox="0 0 12 12"><path d="M2.5 0 4.5 2.5 3.3 4a7 7 0 0 0 4.7 4.7L9.5 7.5 12 9.5 10.5 12C5 12 0 7 0 1.5z"/></svg>503-555-0148</li>
    <li><svg class="icon" viewBox="0 0 12 12"><path d="M3 0h6v12H3zM4 1.5v8h4v-8z"/></svg>503-555-0193</li>
    <li><svg class="icon" viewBox="0 0 12 12"><path d="M0 2h12v8H0zM1 3v.4l5 3.4 5-3.4V3z"/></svg>info@realestatesummitalliance.com</li>
    <li><svg class="icon" viewBox="0 0 12 12"><path d="M6 0a6 6 0 1 0 0 12A6 6 0 0 0 6 0zm0 1c.8.8 1.4 2.4 1.5 4.5h-3C4.6 3.4 5.2 1.8 6 1zM1 6.5h2.5c.1 1.8.6 3.3 1.3 4.3A5 5 0 0 1 1 6.5zm0-1a5 5 0 0 1 3.8-4.3C4.1 2.2 3.6 3.7 3.5 5.5zm5 5.5c-.8-.8-1.4-2.4-1.5-4.5h3c-.1 2.1-.7 3.7-1.5 4.5zm1.2-.2c.7-1 1.2-2.5 1.3-4.3H11a5 5 0 0 1-3.8 4.3zM8.5 5.5c-.1-1.8-.6-3.3-1.3-4.3A5 5 0 0 1 11 5.5z"/></svg>www.RealEstateSummitAlliance.com</li>
  </ul>
</section>

<section class="card card-back" aria-label="Business card back">
  <p class="back-firm">Real Estate<br>Summit Alliance</p>
  <p class="back-web">www.realestatesummitalliance.com</p>
</section>

</body>
</html>
```